Venture 482 - Lumora Book Cover

I am looking for a Lumora book cover for my book about "Venture 482".
The Book is Titled:
Venture 482 Ascended
Shaping Outcomes: Paths To Unlocking Cosmic Truths
Author is Dorian Pell
Here is a book description that may help you understand more about it:
Inspired by the genius of Edwin Marlowe, this comprehensive guide delves into the ancient wisdom and cutting-edge science behind the 482 method, a powerful tool for manifesting your desires. Whether you're seeking personal growth, financial success, or spiritual enlightenment, this book provides advanced techniques and methods to transform your dreams into reality.
Any questions please ask.
Thanks
Owen

```html
<!DOCTYPE html>
<html lang="en">
<head>
<meta charset="utf-8">
<title>Venture 482 Ascended — Dorian Pell</title>
<link href="https://fonts.googleapis.com/css2?family=Cinzel:wght@400;500&family=Tinos&display=swap" rel="stylesheet">
<style>
  :root {
    --page: #e9e9e7;
    --space-deep: #0b0806;
    --space-warm: #3a2410;
    --gold: #c9b07a;
    --gold-light: #e6d3a0;
    --gold-dark: #a88d55;
    --copper: #c0784a;
    --ivory: #fbeee4;
    --line-dark: #0a0a0a;
  }
  html, body {
    margin: 0;
    width: 1200px;
    height: 1131px;
    overflow: hidden;
    background: var(--page);
  }
  .cover {
    position: absolute;
    left: 228px;
    top: 0;
    width: 744px;
    height: 1131px;
    display: block;
  }
  .title-word {
    font-family: "Cinzel", serif;
    font-size: 112px;
    fill: var(--ivory);
    text-anchor: middle;
  }
  .title-digit {
    font-family: "Cinzel", serif;
    font-size: 250px;
    fill: var(--ivory);
    text-anchor: middle;
  }
  .edition {
    font-family: "Cinzel", serif;
    font-size: 42px;
    letter-spacing: 30px;
    fill: var(--ivory);
    text-anchor: middle;
  }
  .subtitle-head {
    font-family: "Tinos", serif;
    font-size: 28px;
    fill: var(--ivory);
    text-anchor: middle;
  }
  .subtitle-line {
    font-family: "Tinos", serif;
    font-size: 24px;
    fill: var(--ivory);
    text-anchor: middle;
  }
  .author {
    font-family: "Cinzel", serif;
    font-size: 50px;
    letter-spacing: 20px;
    fill: var(--ivory);
    text-anchor: middle;
  }
</style>
</head>
<body>
<svg class="cover" viewBox="0 0 875 1330" xmlns="http://www.w3.org/2000/svg">
  <defs>
    <radialGradient id="cosmos" cx="0.55" cy="0.6" r="0.8">
      <stop offset="0" stop-color="var(--space-warm)"/>
      <stop offset="0.35" stop-color="#24170c"/>
      <stop offset="1" stop-color="var(--space-deep)"/>
    </radialGradient>
    <radialGradient id="ornament-glow" cx="0.5" cy="0.5" r="0.5">
      <stop offset="0" stop-color="var(--gold)" stop-opacity="0.28"/>
      <stop offset="1" stop-color="var(--gold)" stop-opacity="0"/>
    </radialGradient>
    <radialGradient id="numeral-glow" cx="0.5" cy="0.5" r="0.5">
      <stop offset="0" stop-color="var(--copper)" stop-opacity="0.22"/>
      <stop offset="1" stop-color="var(--copper)" stop-opacity="0"/>
    </radialGradient>
    <linearGradient id="foil" x1="0" y1="0" x2="1" y2="1">
      <stop offset="0" stop-color="var(--gold-light)"/>
      <stop offset="0.5" stop-color="var(--gold)"/>
      <stop offset="1" stop-color="var(--gold-dark)"/>
    </linearGradient>
  </defs>

  <rect class="cosmic-backdrop" x="0" y="0" width="875" height="1330" fill="url(#cosmos)" role="img" aria-label="Starry nebula background in warm gold and deep black"/>

  <rect class="foil-band" x="93" y="870" width="682" height="342" fill="url(#foil)"/>

  <path class="arch-outer" d="M93,870 V440 A341,341 0 0 1 775,440 V870" fill="var(--line-dark)" stroke="var(--gold)" stroke-width="2"/>
  <path class="arch-ring" d="M108,870 V440 A326,326 0 0 1 760,440 V870" fill="none" stroke="var(--gold)" stroke-width="1.2"/>
  <path class="arch-ring" d="M120,870 V440 A314,314 0 0 1 748,440 V870" fill="none" stroke="var(--gold)" stroke-width="1.2"/>
  <path class="arch-panel" d="M131,1175 V440 A303,303 0 0 1 737,440 V1175 Z" fill="var(--space-deep)"/>
  <path class="arch-panel-glow" d="M131,1175 V440 A303,303 0 0 1 737,440 V1175 Z" fill="url(#cosmos)" opacity="0.55"/>

  <ellipse class="celestial-ornament" cx="437" cy="240" rx="390" ry="110" fill="url(#ornament-glow)" role="img" aria-label="Gold celestial ornament with crescent moon, sun and stars along the arch top"/>

  <text class="title-word" x="437" y="450">VENTURE</text>

  <ellipse class="numeral-ornament" cx="434" cy="648" rx="300" ry="170" fill="url(#numeral-glow)" role="img" aria-label="Copper ornament of rounded frames framing the numerals"/>

  <text class="title-digit" x="243" y="745">4</text>
  <text class="title-digit" x="432" y="745">8</text>
  <text class="title-digit" x="627" y="745">2</text>

  <text class="edition" x="452" y="875">ASCENDED</text>

  <text class="subtitle-head" x="437" y="1000">SHAPING OUTCOMES:</text>
  <text class="subtitle-line" x="437" y="1048">Paths to unlocking</text>
  <text class="subtitle-line" x="437" y="1082">cosmic truths</text>

  <text class="author" x="447" y="1278">DORIAN PELL</text>
</svg>
</body>
</html>
```